Rebrand & reskin fitbrisko.com (Uncoded)

Fitbrisko.com is a commerce website and app for sports and fitness classes and events. In order to improve its appeal, we invite designers to provide their 'skins' for the landing page, club page and event page. Designers can propose using alternate controls and layouts for these pages, and comment on ways to improve the site's usability. It must remain easy to use on a portrait mobile phone screen, responsive design where necessary to also provide a good experience on desktop.

Please navigate to fitbrisko.com and explore the site, and we look forwards to your suggestions!

Target Market(s)

Primary: Tech-savvy mobile users. Secondary: Desktop users

Industry/Entity Type

Health And Wellness

Number of Pages Required

3 page

Font styles to use
Sans Serif

Colors
ffffff
f37122

Requirements
Must have
• This brief is all about changing the look and feel of the site; the winning design will have an immediate 'wow' factor, yet not sacrifice the ease of finding and paying for classes. It must retain the logo, white and orange must be the primary colours used.
Should not have
• The colour palette must remain roughly as is; for example, a very dark site will not appeal.

```html
<!DOCTYPE html>
<html lang="en">
<head>
<meta charset="utf-8">
<title>Fitbrisko – Events</title>
<link rel="stylesheet" href="https://fonts.googleapis.com/css2?family=Open+Sans:wght@400;600&family=Roboto:wght@400;500&display=swap">
<style>
:root{
  --orange:#f37122;
  --orange-dark:#ee5a1a;
  --white:#ffffff;
  --slate:#4a4a55;
  --slate-dark:#3c3c46;
  --row-top:#5a5a66;
  --row-bottom:#3a3a44;
  --page:#efeeec;
  --footer:#2e2e31;
  --text:#4b4b4b;
  --muted:#8a8a8a;
  --rule:#d9d9d9;
}
*{box-sizing:border-box;margin:0;padding:0}
html,body{width:1200px;height:928px;overflow:hidden}
body{position:relative;background:var(--page);font-family:'Roboto',sans-serif;color:var(--text)}
.site-header{position:absolute;left:0;top:0;width:1200px;height:102px;background:var(--white);border-bottom:1px solid var(--rule)}
.brand{position:absolute;left:117px;top:36px;display:flex;align-items:center;gap:10px}
.brand-dot{width:24px;height:24px;border-radius:50%;background:var(--orange)}
.brand-name{font-family:'Roboto',sans-serif;font-weight:500;font-size:27px;letter-spacing:1px;color:var(--orange)}
.main-nav{position:absolute;top:0;left:421px;height:102px;display:flex}
.main-nav a{display:flex;align-items:center;justify-content:center;height:102px;font-size:17px;color:#555;text-decoration:none;letter-spacing:.3px;border-right:1px solid var(--rule)}
.main-nav a:last-child{border-right:none}
.main-nav .active{background:linear-gradient(#4a4a4f,#2c2c30);color:var(--white)}
.sidebar{position:absolute;left:105px;top:102px;width:223px;height:767px;background:var(--slate)}
.side-item{display:flex;align-items:center;height:57px;padding-left:67px;position:relative;color:var(--white);font-size:17px;border-bottom:1px solid #5e5e69}
.side-item:first-child{height:70px}
.side-item svg{position:absolute;left:30px;top:50%;transform:translateY(-50%)}
.page-title{position:absolute;left:366px;top:145px;font-size:30px;font-weight:400;color:#4a4a4f;letter-spacing:1px}
.accordion{position:absolute;left:364px;top:206px;width:708px}
.acc-head{height:43px;display:flex;align-items:center;justify-content:space-between;padding:0 20px;color:var(--white);font-size:16.5px;font-weight:500;letter-spacing:.3px;background:linear-gradient(var(--row-top),var(--row-bottom));border-bottom:1px solid #8a8a94}
.acc-head.open{background:linear-gradient(#f58a35,var(--orange-dark));border-bottom:none}
.acc-body{height:213px;background:var(--white);border:1px solid var(--rule);border-top:none;position:relative}
.event-photo{position:absolute;left:30px;top:26px;width:158px;height:158px;border-radius:50%;background:radial-gradient(circle at 50% 40%,#b7a48e,#6f8a4e 60%,#4d6a35)}
.event-info{position:absolute;left:202px;top:32px;width:470px}
.event-title{font-family:'Open Sans',sans-serif;font-size:17px;color:var(--orange);font-weight:400}
.event-text{font-family:'Open Sans',sans-serif;font-size:12.7px;line-height:21px;color:var(--muted);margin-top:6px}
.event-date{font-family:'Open Sans',sans-serif;font-size:13px;color:#333;margin-top:8px}
.site-footer{position:absolute;left:0;top:869px;width:1200px;height:59px;background:var(--footer);display:flex;align-items:center;justify-content:center;font-family:'Open Sans',sans-serif;font-size:14px;color:#bdbdbd}
</style>
</head>
<body>
<header class="site-header">
  <div class="brand"><span class="brand-dot"></span><span class="brand-name">FITBRISKO</span></div>
  <nav class="main-nav">
    <a style="width:154px">CALENDAR</a>
    <a style="width:110px">FEED</a>
    <a style="width:142px">NEAR BY</a>
    <a style="width:139px">CLASSES</a>
    <a class="active" style="width:115px">EVENT</a>
  </nav>
</header>

<aside class="sidebar">
  <div class="side-item">
    <svg width="26" height="22" viewBox="0 0 26 22"><path d="M14 2h8a2 2 0 0 1 2 2v14a2 2 0 0 1-2 2h-8" fill="none" stroke="#fff" stroke-width="2.5"/><path d="M2 8h8V3l8 8-8 8v-5H2z" fill="#fff"/></svg>
    LOGIN
  </div>
  <div class="side-item">
    <svg width="26" height="28" viewBox="0 0 26 28"><rect x="3" y="2" width="20" height="24" rx="2" fill="none" stroke="#fff" stroke-width="2.2"/><rect x="7" y="2" width="4" height="8" fill="#fff"/><path d="M15 13l1.5 3 3 .4-2.2 2 .6 3-2.9-1.5-2.9 1.5.6-3-2.2-2 3-.4z" fill="#fff"/></svg>
    MY DIARY
  </div>
  <div class="side-item">
    <svg width="34" height="34" viewBox="0 0 34 34"><path d="M17 1l16 16-16 16L1 17z" fill="#fff"/><rect x="8" y="15" width="18" height="4" fill="var(--slate)"/><rect x="8" y="11" width="4" height="12" fill="var(--slate)"/><rect x="22" y="11" width="4" height="12" fill="var(--slate)"/></svg>
    MY CLUBS
  </div>
  <div class="side-item">
    <svg width="26" height="26" viewBox="0 0 26 26"><circle cx="13" cy="7" r="6" fill="#fff"/><path d="M1 26v-5a7 7 0 0 1 7-7h10a7 7 0 0 1 7 7v5z" fill="#fff"/></svg>
    MY PROFILE
  </div>
</aside>

<h1 class="page-title">EVENTS</h1>

<section class="accordion">
  <div class="acc-head open">EVENT TITTLE HERE
    <svg width="22" height="12" viewBox="0 0 22 12"><path d="M1 11L11 2l10 9" fill="none" stroke="#fff" stroke-width="1.8"/></svg>
  </div>
  <div class="acc-body">
    <div class="event-photo" role="img" aria-label="Smiling runner crossing the finish line tape outdoors"></div>
    <div class="event-info">
      <h2 class="event-title">Proin nulla arcu nonummy luctus</h2>
      <p class="event-text">Praesent sit amet est In dictum dolor eu dictum porttitor enim felis viverra mi eget luctus massa purus quis odio Etiam nulla massa pharetra facilisis volutpat in imperdiet sit amet sem Aliquam nec erat at purus cursus interdum bibendum accumsan vestibulum ut commodo a mi Morbi ornare</p>
      <p class="event-date">25 Aug 2016</p>
    </div>
  </div>
  <div class="acc-head">EVENT TITTLE HERE<svg width="22" height="12" viewBox="0 0 22 12"><path d="M1 1l10 9 10-9" fill="none" stroke="#fff" stroke-width="1.8"/></svg></div>
  <div class="acc-head">EVENT TITTLE HERE<svg width="22" height="12" viewBox="0 0 22 12"><path d="M1 1l10 9 10-9" fill="none" stroke="#fff" stroke-width="1.8"/></svg></div>
  <div class="acc-head">EVENT TITTLE HERE<svg width="22" height="12" viewBox="0 0 22 12"><path d="M1 1l10 9 10-9" fill="none" stroke="#fff" stroke-width="1.8"/></svg></div>
  <div class="acc-head">EVENT TITTLE HERE<svg width="22" height="12" viewBox="0 0 22 12"><path d="M1 1l10 9 10-9" fill="none" stroke="#fff" stroke-width="1.8"/></svg></div>
</section>

<footer class="site-footer">© 2016 Company Name&nbsp; All right reserved&nbsp; Term of Use</footer>
</body>
</html>
```